Movie poster for short film: TINFOIL

We need a creative, artistic, stylized poster design for our short film TINFOIL. We would like to see designs with graphics and bold colors more than photographs. The photographs we are posting are more for reference- you do not have to use them in the poster! We are looking for something clean and simple. The film is a drama so please don't make it funny. The mood of the film is thoughtful and introspective. Name of film should be in all caps. Things to include in the poster:
Name of film: TINFOIL
Paper Lantern Productions
Starring Marta Kowelski

Here is a brief plot synopsis: TINFOIL follows one night in the life of a rebellious young woman who breaks into a diner after hours with a can of spray paint. Her intentions change after she ends up discovering what's left of a love story.

The movie is somewhat experimental, set to music for part of it with no dialog. The whole movie takes place in an old fashioned diner.

Target Market(s)

Film festival attendees between the ages of 20-50

Industry/Entity Type

Movie

Font styles to use
Sans Serif

Requirements
Must have
• See project description above- also the film is somewhat dark in nature so please don't make it too 'happy' looking.

```html
<!DOCTYPE html>
<html lang="en">
<head>
<meta charset="utf-8">
<title>TINFOIL — Poster</title>
<link rel="stylesheet" href="https://fonts.googleapis.com/css2?family=Jost:wght@400;500&display=swap">
<style>
  :root {
    --ink: #000000;
    --paper: #ffffff;
    --key-red: #d0222b;
  }
  html, body {
    margin: 0;
    padding: 0;
    width: 960px;
    height: 1200px;
    overflow: hidden;
    background: var(--ink);
  }
  .poster {
    position: relative;
    width: 960px;
    height: 1200px;
    background: var(--ink);
    font-family: "Jost", "Futura", sans-serif;
    color: var(--paper);
  }
  .poster-type {
    position: absolute;
    inset: 0;
    width: 960px;
    height: 1200px;
  }
  .studio-credit {
    font-family: "Jost", sans-serif;
    font-weight: 500;
    font-size: 27px;
    fill: var(--paper);
  }
  .film-title {
    font-family: "Jost", sans-serif;
    font-weight: 500;
    font-size: 144px;
    fill: var(--paper);
  }
  .billing-label {
    font-family: "Jost", sans-serif;
    font-weight: 500;
    font-size: 24px;
    letter-spacing: 0.18em;
    fill: var(--paper);
  }
  .billing-name {
    font-family: "Jost", sans-serif;
    font-weight: 400;
    font-size: 44px;
    letter-spacing: 0.12em;
    fill: var(--paper);
  }
  .key-art {
    position: absolute;
    left: 138px;
    top: 355px;
    width: 684px;
    height: 684px;
    border-radius: 50%;
    background: var(--key-red);
  }
</style>
</head>
<body>
<main class="poster">
  <div class="key-art" role="img" aria-label="Key art for TINFOIL: a single central red round artwork on black"></div>
  <svg class="poster-type" viewBox="0 0 960 1200" xmlns="http://www.w3.org/2000/svg">
    <text class="studio-credit" x="480" y="68" text-anchor="middle">Paper Lantern Productions</text>
    <text class="studio-credit" x="480" y="98" text-anchor="middle">Presents</text>

    <text class="film-title" x="102" y="250" textLength="760" lengthAdjust="spacing">TINFOIL</text>

    <text class="billing-label" x="482" y="1090" text-anchor="middle">Starring</text>
    <text class="billing-name" x="482" y="1131" text-anchor="middle">Marta Kowelski</text>
  </svg>
</main>
</body>
</html>
```